Logo, Web and Mobile Designs for enterprise social media platform

All the details are in the attached document, please start reading the scope document first which explains what is this project about and the details about the needed deliverables, after that please read the UI_Requirements document which will detail what is expected regarding the coded web version since this is a coded contest, it is very important that you meet the UI requirements or suggest something else but we will need to agree first before working on the coded version

Good Luck

Target Market(s)

Enterprise Social Media

Industry/Entity Type

Media

Coding

Coded - Design and coding required

Number of Pages Required

5+ page

Font styles to use
Sans Serif

Requirements
Must have
• All the must haves are listed in the scope document so please check before you start

```html
<!DOCTYPE html>
<html lang="en">
<head>
<meta charset="utf-8">
<title>Teamora – Most Recent Posts</title>
<link href="https://fonts.googleapis.com/css2?family=Roboto:wght@300;400;500;700&display=swap" rel="stylesheet">
<style>
:root{
  --bg:#f1f1f1;
  --card:#ffffff;
  --line:#e4e4e4;
  --header:#222222;
  --brand:#f2c318;
  --accent:#e9534a;
  --text:#333333;
  --muted:#8a8a8a;
  --soft:#f6f6f6;
  --online:#3aa63a;
  --icon:#9a9a9a;
}
*{box-sizing:border-box;margin:0;padding:0}
html,body{width:1200px;height:2413px;overflow:hidden}
body{background:var(--bg);font-family:"Roboto",Arial,sans-serif;color:var(--text);position:relative;font-size:12px}
svg{display:block}

/* header */
.topbar{position:absolute;left:0;top:0;width:1200px;height:60px;background:var(--header)}
.brand{position:absolute;left:100px;top:12px;font-size:32px;font-weight:400;color:var(--brand);letter-spacing:.3px}
.welcome{position:absolute;right:265px;top:23px;color:#ddd;font-size:11.5px}
.top-tools{position:absolute;left:960px;top:0;height:60px;display:flex}
.tool{width:49px;height:60px;border-left:1px solid #3a3a3a;display:flex;flex-direction:column;align-items:center;justify-content:center;gap:5px;color:#ddd;font-size:10px}
.tool:last-child{border-right:1px solid #3a3a3a}
.tool.badge{color:var(--brand)}

/* left column */
.sidebar{position:absolute;left:100px;top:85px;width:170px}
.avatar-xl{width:166px;height:165px;border:4px solid #fff;box-shadow:0 0 0 1px var(--line);background:linear-gradient(160deg,#c9c2b8,#5e5a57 70%,#2b2b30)}
.me-name{margin-top:20px;font-size:13.5px;font-weight:500}
.me-city{font-size:11px;color:var(--muted);margin-top:2px}
.rule{height:1px;background:#d8d8d8;margin:15px 0 16px}
.nav{list-style:none}
.nav li{height:34.3px;display:flex;align-items:center;gap:12px;font-size:12px;color:#444}
.nav li.active{color:var(--accent)}
.nav svg{width:13px;height:13px;fill:#555}
.nav li.active svg{fill:var(--accent)}
.social-nav li .dot{width:11px;height:11px;border-radius:50%;background:#555}
.ad-tall{width:101px;height:513px;background:linear-gradient(180deg,#4a6e8e,#9db5c9 40%,#6f8a4e 75%,#2e3a25)}

/* centre feed */
.feed{position:absolute;left:283px;top:84px;width:547px}
.box{background:var(--card);border:1px solid var(--line)}
.search{height:48px;display:flex;align-items:center;justify-content:space-between;padding:0 17px;color:var(--muted);font-size:11.5px}
.composer{margin-top:13px;height:106px}
.composer-top{height:48px;display:flex;align-items:center;justify-content:space-between;padding:0 17px;color:var(--muted);font-size:11.5px;border-bottom:1px solid var(--line)}
.composer-actions{display:flex;justify-content:space-between;padding:18px 24px 0 17px}
.composer-actions span{display:flex;align-items:center;gap:7px;color:#aaa;font-size:11px}
.composer-actions svg{width:16px;height:14px;fill:#bbb}

.posts{margin-top:16px;display:flex;flex-direction:column;gap:18px}
.post{height:646px;position:relative}
.post-head{height:85px;padding:10px 11px 0;display:flex;gap:12px;position:relative}
.avatar-m{width:58px;height:59px;background:linear-gradient(170deg,#d8d0c6,#7a6f66 60%,#35353a)}
.post-who{padding-top:6px}
.post-who b{display:block;font-size:11.5px;font-weight:500}
.post-who small{display:block;font-size:9.5px;color:var(--muted);margin-top:4px}
.post-who time{display:block;font-size:9.5px;color:#666;margin-top:19px}
.post-ctrl{position:absolute;right:12px;top:10px;display:flex;gap:13px;color:#999;font-size:11px}
.media{margin:0 11px;height:264px}
.media.meeting{background:linear-gradient(135deg,#cdd8e4,#7b8ea6 45%,#2f3e57)}
.media.video{background:linear-gradient(135deg,#8d949b,#515a63 50%,#2f3338);display:flex;align-items:center;justify-content:center}
.media.team{background:linear-gradient(135deg,#c9a67f,#8a6d53 45%,#4b5a66)}
.play{width:54px;height:54px;border-radius:50%;border:2px solid rgba(255,255,255,.85);background:rgba(0,0,0,.25);display:flex;align-items:center;justify-content:center;padding-left:4px}
.post-body{margin:24px 11px 0;font-size:11.4px;line-height:19.6px;color:#555}
.post-stats{display:flex;gap:30px;margin:16px 11px 0;font-size:9.5px;color:#666;align-items:center}
.post-stats span{display:flex;align-items:center;gap:6px}
.post-stats svg{width:13px;height:10px;fill:#666}
.comments{position:absolute;left:0;right:0;bottom:0;height:150px;background:var(--soft);padding:0 11px}
.comments-bar{height:42px;display:flex;align-items:flex-end;justify-content:space-between;padding:0 4px 6px;font-size:9.5px;color:#666}
.comments-bar span{display:flex;align-items:center;gap:6px}
.comment{display:flex;gap:14px;margin-top:7px;padding-left:5px}
.avatar-s{width:58px;height:59px;flex:none;background:linear-gradient(170deg,#d4cbc1,#80736a 60%,#3a3a3f)}
.comment-main{flex:1;border-top:1px solid #ddd;padding-top:6px}
.comment-main header{font-size:9.5px;color:#666}
.comment-main header b{font-size:11px;color:var(--text);font-weight:500;margin-right:6px}
.comment-main p{margin-top:13px;font-size:9.3px;line-height:15.5px;color:#555}
.reload{position:absolute;left:548px;top:2272px}

/* right column */
.aside{position:absolute;left:843px;top:84px;width:257px;display:flex;flex-direction:column;gap:14px}
.widget{padding:0 8px}
.widget h3{height:40px;display:flex;align-items:center;gap:7px;font-size:13px;font-weight:500;color:var(--accent);border-bottom:1px solid var(--line);margin:0 -8px;padding-left:12px}
.friends{height:423px}
.friend{display:flex;gap:14px;height:61.8px;align-items:flex-start}
.friend:first-of-type{margin-top:15px}
.face{width:40px;height:43px;flex:none;background:linear-gradient(170deg,#d9d1c8,#7d7068 60%,#3a3a3f)}
.friend > div:last-child{min-width:0}
.friend b{display:block;font-size:11px;font-weight:500;margin-top:1px}
.friend small{display:block;font-size:7px;color:#888;margin-top:3px;line-height:10px;white-space:nowrap}
.friend .on{color:var(--online);font-size:9px;margin-top:6px;display:block}
.friend .off{color:#888;font-size:9px;margin-top:6px;display:block}
.list-widget{height:427px}
.item{display:flex;gap:9px;height:85px}
.item:first-of-type{margin-top:20px}
.thumb{width:90px;height:68px;flex:none}
.t1{background:linear-gradient(135deg,#9fb3c7,#4f6377)}
.t2{background:linear-gradient(135deg,#c7c1b6,#6b6660)}
.t3{background:linear-gradient(135deg,#b5cbd8,#5f7e93)}
.t4{background:linear-gradient(135deg,#8a8f96,#3d4249)}
.t5{background:linear-gradient(135deg,#8fa9bf,#345068)}
.t6{background:linear-gradient(135deg,#b5b2ae,#3f3f42)}
.t7{background:linear-gradient(135deg,#7bb1cf,#475e6f)}
.t8{background:linear-gradient(135deg,#a58769,#5d6c57)}
.t9{background:linear-gradient(135deg,#a5a6ab,#4e4c55)}
.t10{background:linear-gradient(135deg,#b58d6f,#5c4a45)}
.t11{background:linear-gradient(135deg,#9c7b62,#4a3a33)}
.t12{background:linear-gradient(135deg,#d69b5a,#5a3a2a)}
.item b{display:block;font-size:10.5px;font-weight:500;margin-top:1px}
.item small{display:block;font-size:7.8px;color:#888;line-height:10.5px;margin-top:5px}
.view-all{font-size:8.5px;color:#999;letter-spacing:.4px;padding-left:4px;margin-top:-6px}
.ad-wide{height:213px;background:linear-gradient(180deg,#7fc241 0 14%,#1f4f86 14% 75%,#ffffff 75%);border:1px solid var(--line)}

/* footer */
.footer{position:absolute;left:0;top:2328px;width:1200px;height:85px;background:#fafafa;border-top:1px solid var(--line)}
.copy{position:absolute;left:100px;top:36px;font-size:11.5px;color:#555}
.social-dots{position:absolute;left:896px;top:28px;display:flex;gap:7px}
.social-dots i{width:28px;height:28px;border-radius:50%;display:block}
</style>
</head>
<body>
<svg width="0" height="0" style="position:absolute">
  <defs>
    <symbol id="i-user" viewBox="0 0 12 12"><circle cx="6" cy="3.5" r="2.8"/><path d="M0 12c0-3.5 2.7-5 6-5s6 1.5 6 5z"/></symbol>
    <symbol id="i-cal" viewBox="0 0 12 12"><path d="M0 2h12v10H0zM1 5v6h10V5z"/><rect x="2" y="0" width="2" height="3"/><rect x="8" y="0" width="2" height="3"/></symbol>
    <symbol id="i-bell" viewBox="0 0 12 12"><path d="M6 0a4 4 0 0 1 4 4v4l2 2H0l2-2V4a4 4 0 0 1 4-4z"/><circle cx="6" cy="11" r="1.3"/></symbol>
    <symbol id="i-list" viewBox="0 0 12 12"><rect x="0" y="1" width="12" height="2"/><rect x="0" y="5" width="12" height="2"/><rect x="0" y="9" width="12" height="2"/></symbol>
    <symbol id="i-chat" viewBox="0 0 12 12"><ellipse cx="6" cy="5" rx="6" ry="4.5"/><path d="M2 8l-1 4 4-2.5z"/></symbol>
    <symbol id="i-cam" viewBox="0 0 12 12"><path d="M0 3h3l1.5-2h3L9 3h3v8H0z"/><circle cx="6" cy="7" r="2.2" fill="#fff"/></symbol>
    <symbol id="i-video" viewBox="0 0 12 12"><rect x="0" y="3" width="8" height="7" rx="1"/><path d="M8 6l4-3v7l-4-3z"/></symbol>
    <symbol id="i-horn" viewBox="0 0 12 12"><path d="M0 4h3l7-4v12L3 8H0z"/></symbol>
    <symbol id="i-plus" viewBox="0 0 12 12"><circle cx="6" cy="6" r="6"/><path d="M5 3h2v2h2v2H7v2H5V7H3V5h2z" fill="#fff"/></symbol>
    <symbol id="i-doc" viewBox="0 0 12 12"><path d="M1 0h7l3 3v9H1z"/><path d="M3 5h6v1H3zM3 7h6v1H3zM3 9h4v1H3z" fill="#fff"/></symbol>
    <symbol id="i-mic" viewBox="0 0 12 12"><rect x="4" y="0" width="4" height="8" rx="2"/><path d="M2 6a4 4 0 0 0 8 0h-1a3 3 0 0 1-6 0zM5.5 10h1v2h-1z"/></symbol>
    <symbol id="i-eye" viewBox="0 0 14 10"><path d="M0 5C2 1 5 0 7 0s5 1 7 5c-2 4-5 5-7 5S2 9 0 5z"/><circle cx="7" cy="5" r="2.2" fill="#fff"/></symbol>
    <symbol id="i-share" viewBox="0 0 14 10"><path d="M8 0l6 4.5L8 9V6C4 6 2 7.5 0 10c1-5 4-7 8-7z"/></symbol>
  </defs>
</svg>

<header class="topbar">
  <div class="brand">Teamora</div>
  <div class="welcome">Welcome, John Cole</div>
  <nav class="top-tools">
    <div class="tool"><svg width="14" height="14" fill="#ddd"><use href="#i-user"/></svg>18</div>
    <div class="tool badge"><svg width="15" height="14" fill="#f2c318"><use href="#i-chat"/></svg>2</div>
    <div class="tool">
      <svg width="15" height="15" viewBox="0 0 16 16" fill="#ddd"><circle cx="8" cy="8" r="5.5"/><g stroke="#ddd" stroke-width="2.6"><path d="M8 0v16M0 8h16M2.3 2.3l11.4 11.4M13.7 2.3L2.3 13.7"/></g><circle cx="8" cy="8" r="2.2" fill="#222"/></svg>
      <svg width="9" height="6" viewBox="0 0 9 6"><path d="M1 1l3.5 3.5L8 1" stroke="#ddd" stroke-width="1.6" fill="none"/></svg>
    </div>
  </nav>
</header>

<aside class="sidebar">
  <div class="avatar-xl" role="img" aria-label="Profile portrait of John Cole"></div>
  <div class="me-name">John Cole</div>
  <div class="me-city">New York</div>
  <div class="rule"></div>
  <ul class="nav">
    <li class="active"><svg><use href="#i-doc"/></svg>Most Recent Post</li>
    <li><svg><use href="#i-user"/></svg>Post from Friends</li>
    <li><svg><use href="#i-user"/></svg>Post from Groups</li>
    <li><svg><use href="#i-cal"/></svg>Events</li>
    <li><svg><use href="#i-bell"/></svg>Reminder</li>
    <li><svg><use href="#i-list"/></svg>Topics</li>
    <li><svg><use href="#i-chat"/></svg>Messages</li>
    <li><svg><use href="#i-cam"/></svg>Photos</li>
    <li><svg><use href="#i-video"/></svg>Videos</li>
    <li><svg><use href="#i-horn"/></svg>Announcements</li>
    <li><svg><use href="#i-plus"/></svg>Create a Group</li>
    <li><svg><use href="#i-plus"/></svg>Create Event</li>
  </ul>
  <div class="rule" style="margin-top:15px"></div>
  <ul class="nav social-nav">
    <li><span class="dot" style="background:#3b5998"></span><span style="color:#3b5998">Friendnet</span></li>
    <li><span class="dot"></span>Chirpline</li>
    <li><span class="dot"></span>Worklinks</li>
    <li><span class="dot"></span>Circleplus</li>
    <li><span class="dot"></span>Viewtube</li>
    <li><svg viewBox="0 0 12 12"><path d="M0 2h12v8H0z"/><path d="M0 2l6 5 6-5" stroke="#fff" fill="none"/></svg>Email</li>
  </ul>
  <div class="rule" style="margin-top:15px;margin-bottom:16px"></div>
  <div class="ad-tall" role="img" aria-label="Stridelab running shoe advertisement with a footballer"></div>
</aside>

<main class="feed">
  <div class="box search">
    <span>Search Post, Event or User</span>
    <svg width="14" height="14" viewBox="0 0 14 14"><circle cx="6" cy="6" r="4.5" stroke="#f2c318" stroke-width="2" fill="none"/><path d="M9.5 9.5L13 13" stroke="#f2c318" stroke-width="2.4"/></svg>
  </div>
  <div class="box composer">
    <div class="composer-top">
      <span>What's New</span>
      <svg width="14" height="14" viewBox="0 0 14 14"><circle cx="7" cy="7" r="6" stroke="#bbb" fill="none"/><circle cx="5" cy="5.5" r=".9" fill="#bbb"/><circle cx="9" cy="5.5" r=".9" fill="#bbb"/><path d="M4 8.5a3.2 3.2 0 0 0 6 0" stroke="#bbb" fill="none"/></svg>
    </div>
    <div class="composer-actions">
      <span><svg viewBox="0 0 12 12"><use href="#i-doc"/></svg>Post</span>
      <span><svg viewBox="0 0 12 12"><use href="#i-cam"/></svg>Photos</span>
      <span><svg viewBox="0 0 12 12"><use href="#i-video"/></svg>Videos</span>
      <span><svg viewBox="0 0 14 14"><path d="M5 9l4-4" stroke="#bbb" stroke-width="1.6"/><rect x="1" y="6" width="6" height="4" rx="2" transform="rotate(-45 4 8)" stroke="#bbb" stroke-width="1.4" fill="none"/><rect x="7" y="2" width="6" height="4" rx="2" transform="rotate(-45 10 4)" stroke="#bbb" stroke-width="1.4" fill="none"/></svg>Link</span>
      <span><svg viewBox="0 0 12 12"><use href="#i-cal"/></svg>Events</span>
      <span><svg viewBox="0 0 12 12"><rect x="0" y="6" width="2.5" height="6"/><rect x="3.5" y="2" width="2.5" height="10"/><rect x="7" y="4" width="2.5" height="8"/><rect x="10" y="0" width="2" height="12"/></svg>Poll</span>
    </div>
  </div>

  <div class="posts">
    <article class="box post">
      <div class="post-head">
        <div class="avatar-m" role="img" aria-label="Avatar of John Cole"></div>
        <div class="post-who"><b>John Cole</b><small>New York</small><time>18 November, 2015 &nbsp; at &nbsp;10.15 A.M</time></div>
        <div class="post-ctrl"><span>&#8964;</span><span>&#10005;</span></div>
      </div>
      <div class="media meeting" role="img" aria-label="Business team shaking hands in a bright office"></div>
      <p class="post-body">Aenean sed quam non sapien faucibus consequat vitae sit amet orci. Praesent quis risus mi. In mollis nulla in pulvinar dictum. Vivamus interdum sagittis felis, ut dapibus ligula feugiat ac. In dictum sapien eu tellus finibus fermentum. Aenean faucibus lacus ut mollis commodo. Donec vestibulum odio sem, ac laoreet massa ullamcorper id. Donec molestie nisi et tellus hendrerit vehicula.</p>
      <div class="post-stats"><span><svg viewBox="0 0 14 10"><use href="#i-eye"/></svg>1,028</span><span><svg viewBox="0 0 14 10"><use href="#i-share"/></svg>Share</span></div>
      <section class="comments">
        <div class="comments-bar"><span><svg width="11" height="10" viewBox="0 0 12 12" fill="#666"><use href="#i-chat"/></svg>52 Comments</span><span>&#8964;</span></div>
        <div class="comment">
          <div class="avatar-s" role="img" aria-label="Avatar of David"></div>
          <div class="comment-main">
            <header><b>David</b>Sydney &nbsp;18 November, 2015 &nbsp; at &nbsp;10.15 A.M</header>
            <p>Phasellus blandit quam a ipsum gravida dapibus. Cras sed augue tortor. Suspendisse elit ligula, iaculis dignissim justo eu, vestibulum venenatis elit. Sed egestas, nisl id cursus ultricies, turpis orci rhoncus odio, id tristique odio ex in lacus. Nam suscipit sapien eget blandit sollicitudin.</p>
          </div>
        </div>
      </section>
    </article>

    <article class="box post">
      <div class="post-head">
        <div class="avatar-m" role="img" aria-label="Avatar of John Cole"></div>
        <div class="post-who"><b>John Cole</b><small>New York</small><time>18 November, 2015 &nbsp; at &nbsp;10.15 A.M</time></div>
        <div class="post-ctrl"><span>&#8964;</span><span>&#10005;</span></div>
      </div>
      <div class="media video" role="img" aria-label="Video still of a meeting around a conference table">
        <div class="play"><svg width="16" height="18" viewBox="0 0 16 18"><path d="M0 0l16 9L0 18z" fill="#fff"/></svg></div>
      </div>
      <p class="post-body">Aenean sed quam non sapien faucibus consequat vitae sit amet orci. Praesent quis risus mi. In mollis nulla in pulvinar dictum. Vivamus interdum sagittis felis, ut dapibus ligula feugiat ac. In dictum sapien eu tellus finibus fermentum. Aenean faucibus lacus ut mollis commodo. Donec vestibulum odio sem, ac laoreet massa ullamcorper id. Donec molestie nisi et tellus hendrerit vehicula.</p>
      <div class="post-stats"><span><svg viewBox="0 0 14 10"><use href="#i-eye"/></svg>1,028</span><span><svg viewBox="0 0 14 10"><use href="#i-share"/></svg>Share</span></div>
      <section class="comments">
        <div class="comments-bar"><span><svg width="11" height="10" viewBox="0 0 12 12" fill="#666"><use href="#i-chat"/></svg>52 Comments</span><span>&#8964;</span></div>
        <div class="comment">
          <div class="avatar-s" role="img" aria-label="Avatar of David"></div>
          <div class="comment-main">
            <header><b>David</b>Sydney &nbsp;18 November, 2015 &nbsp; at &nbsp;10.15 A.M</header>
            <p>Phasellus blandit quam a ipsum gravida dapibus. Cras sed augue tortor. Suspendisse elit ligula, iaculis dignissim justo eu, vestibulum venenatis elit. Sed egestas, nisl id cursus ultricies, turpis orci rhoncus odio, id tristique odio ex in lacus. Nam suscipit sapien eget blandit sollicitudin.</p>
          </div>
        </div>
      </section>
    </article>

    <article class="box post">
      <div class="post-head">
        <div class="avatar-m" role="img" aria-label="Avatar of John Cole"></div>
        <div class="post-who"><b>John Cole</b><small>New York</small><time>18 November, 2015 &nbsp; at &nbsp;10.15 A.M</time></div>
        <div class="post-ctrl"><span>&#8964;</span><span>&#10005;</span></div>
      </div>
      <div class="media team" role="img" aria-label="Young team working together at a desk"></div>
      <p class="post-body">Aenean sed quam non sapien faucibus consequat vitae sit amet orci. Praesent quis risus mi. In mollis nulla in pulvinar dictum. Vivamus interdum sagittis felis, ut dapibus ligula feugiat ac. In dictum sapien eu tellus finibus fermentum. Aenean faucibus lacus ut mollis commodo. Donec vestibulum odio sem, ac laoreet massa ullamcorper id. Donec molestie nisi et tellus hendrerit vehicula.</p>
      <div class="post-stats"><span><svg viewBox="0 0 14 10"><use href="#i-eye"/></svg>1,028</span><span><svg viewBox="0 0 14 10"><use href="#i-share"/></svg>Share</span></div>
      <section class="comments">
        <div class="comments-bar"><span><svg width="11" height="10" viewBox="0 0 12 12" fill="#666"><use href="#i-chat"/></svg>52 Comments</span><span>&#8964;</span></div>
        <div class="comment">
          <div class="avatar-s" role="img" aria-label="Avatar of David"></div>
          <div class="comment-main">
            <header><b>David</b>Sydney &nbsp;18 November, 2015 &nbsp; at &nbsp;10.15 A.M</header>
            <p>Phasellus blandit quam a ipsum gravida dapibus. Cras sed augue tortor. Suspendisse elit ligula, iaculis dignissim justo eu, vestibulum venenatis elit. Sed egestas, nisl id cursus ultricies, turpis orci rhoncus odio, id tristique odio ex in lacus. Nam suscipit sapien eget blandit sollicitudin.</p>
          </div>
        </div>
      </section>
    </article>
  </div>
</main>

<svg class="reload" width="22" height="22" viewBox="0 0 22 22" aria-label="Load more posts"><path d="M4 10a7 7 0 0 1 12.5-4M18 12a7 7 0 0 1-12.5 4" stroke="#9a9a9a" stroke-width="2.6" fill="none"/><path d="M17 1v6h-6zM5 21v-6h6z" fill="#9a9a9a"/></svg>

<aside class="aside">
  <section class="box widget friends">
    <h3><svg width="12" height="12" fill="#e9534a"><use href="#i-user"/></svg>Friends</h3>
    <div class="friend"><div class="face" role="img" aria-label="Avatar of William"></div><div><b>William</b><small>Aliquam dignissim elit nec mauris porta, vitae pretium</small><span class="on">Online</span></div></div>
    <div class="friend"><div class="face" role="img" aria-label="Avatar of Ethan"></div><div><b>Ethan</b><small>Aliquam dignissim elit nec mauris porta, vitae pretium</small><span class="on">Online</span></div></div>
    <div class="friend"><div class="face" role="img" aria-label="Avatar of Michael"></div><div><b>Michael</b><small>Aliquam dignissim elit nec mauris porta, vitae pretium</small><span class="on">Online</span></div></div>
    <div class="friend"><div class="face" role="img" aria-label="Avatar of Alexander"></div><div><b>Alexander</b><small>Aliquam dignissim elit nec mauris porta, vitae pretium</small><span class="on">Online</span></div></div>
    <div class="friend"><div class="face" role="img" aria-label="Avatar of Emma"></div><div><b>Emma</b><small>Aliquam dignissim elit nec mauris porta, vitae pretium</small><span class="off">Offline</span></div></div>
    <div class="friend"><div class="face" role="img" aria-label="Avatar of Madison"></div><div><b>Madison</b><small>Aliquam dignissim elit nec mauris porta, vitae pretium</small><span class="off">Offline</span></div></div>
  </section>

  <section class="box widget list-widget">
    <h3><svg width="12" height="12" fill="#e9534a"><use href="#i-cal"/></svg>Events</h3>
    <div class="item"><div class="thumb t1" role="img" aria-label="Conference event photo"></div><div><b>18 Nov, 2015</b><small>Aenean aliquet risus metus,<br>vitae tristique enim finibus eu.<br>Sed iaculis nisl est.</small></div></div>
    <div class="item"><div class="thumb t2" role="img" aria-label="Team workshop photo"></div><div><b>18 Nov, 2015</b><small>Aenean aliquet risus metus,<br>vitae tristique enim finibus eu.<br>Sed iaculis nisl est.</small></div></div>
    <div class="item"><div class="thumb t3" role="img" aria-label="Startup meetup photo"></div><div><b>18 Nov, 2015</b><small>Aenean aliquet risus metus,<br>vitae tristique enim finibus eu.<br>Sed iaculis nisl est.</small></div></div>
    <div class="item"><div class="thumb t4" role="img" aria-label="Networking evening photo"></div><div><b>18 Nov, 2015</b><small>Aenean aliquet risus metus,<br>vitae tristique enim finibus eu.<br>Sed iaculis nisl est.</small></div></div>
    <div class="view-all">VIEW ALL</div>
  </section>

  <section class="box widget list-widget" style="height:423px">
    <h3><svg width="12" height="12" fill="#e9534a"><use href="#i-doc"/></svg>Articles</h3>
    <div class="item"><div class="thumb t5" role="img" aria-label="Article photo of a businessman"></div><div><b>18 Nov, 2015</b><small>Aenean aliquet risus metus,<br>vitae tristique enim finibus eu.<br>Sed iaculis nisl est.</small></div></div>
    <div class="item"><div class="thumb t6" role="img" aria-label="Article photo of a presenter at a board"></div><div><b>18 Nov, 2015</b><small>Aenean aliquet risus metus,<br>vitae tristique enim finibus eu.<br>Sed iaculis nisl est.</small></div></div>
    <div class="item"><div class="thumb t7" role="img" aria-label="Article photo of charts on a screen"></div><div><b>18 Nov, 2015</b><small>Aenean aliquet risus metus,<br>vitae tristique enim finibus eu.<br>Sed iaculis nisl est.</small></div></div>
    <div class="item"><div class="thumb t8" role="img" aria-label="Article photo of a colleague group"></div><div><b>18 Nov, 2015</b><small>Aenean aliquet risus metus,<br>vitae tristique enim finibus eu.<br>Sed iaculis nisl est.</small></div></div>
    <div class="view-all">VIEW ALL</div>
  </section>

  <section class="box widget list-widget">
    <h3><svg width="12" height="12" fill="#e9534a"><use href="#i-mic"/></svg>Seminars</h3>
    <div class="item"><div class="thumb t9" role="img" aria-label="Seminar audience photo"></div><div><b>18 Nov, 2015</b><small>Aenean aliquet risus metus,<br>vitae tristique enim finibus eu.<br>Sed iaculis nisl est.</small></div></div>
    <div class="item"><div class="thumb t10" role="img" aria-label="Seminar speaker photo"></div><div><b>18 Nov, 2015</b><small>Aenean aliquet risus metus,<br>vitae tristique enim finibus eu.<br>Sed iaculis nisl est.</small></div></div>
    <div class="item"><div class="thumb t11" role="img" aria-label="Lecture hall photo"></div><div><b>18 Nov, 2015</b><small>Aenean aliquet risus metus,<br>vitae tristique enim finibus eu.<br>Sed iaculis nisl est.</small></div></div>
    <div class="item"><div class="thumb t12" role="img" aria-label="Stage presentation photo"></div><div><b>18 Nov, 2015</b><small>Aenean aliquet risus metus,<br>vitae tristique enim finibus eu.<br>Sed iaculis nisl est.</small></div></div>
    <div class="view-all">VIEW ALL</div>
  </section>

  <div class="ad-wide" role="img" aria-label="Uploadmirror banner advertisement for a file mirroring service"></div>
</aside>

<footer class="footer">
  <div class="copy">Copyright &copy; &nbsp;2015 &nbsp;Teamora. &nbsp; All rights reserved.</div>
  <div class="social-dots">
    <i style="background:#3b5998"></i>
    <i style="background:#2aa3dd"></i>
    <i style="background:#1a75b3"></i>
    <i style="background:#dd4b39"></i>
    <i style="background:#d9322a"></i>
    <i style="background:#4caf50"></i>
  </div>
</footer>
</body>
</html>
```